Halverstone Minerals Web Design

Require a Web page design for an international mining and private investment company currently based in Dubai, UAE. I would like to view designs that incorporate our current corporate logo design aimed at communicating global business development/expansion across a diversity of commodities within the mining and investment sectors.

We are a global organisation with global experience and strategy with specific business development focus in Africa, Central and South America.

Target Market(s)

Mining industry, finance, fund raising, brokering, private equity and public stock exchanges.

Industry/Entity Type

Mining

Number of Pages Required

5+ page

Font styles to use
Sans Serif

Colors

Designer to choose colors to be used in the design.

Requirements
Must have
• Corporate logo, description of who we are, what we do, corporate mission, vision & strategy.
Nice to have
• Inclusion of images, photos, interactive maps/graphics and video.

```html
<!DOCTYPE html>
<html lang="en">
<head>
<meta charset="utf-8">
<title>Halverstone Minerals</title>
<link href="https://fonts.googleapis.com/css2?family=Barlow:wght@400;500;600;700&family=Poppins:wght@500;600;700&display=swap" rel="stylesheet">
<style>
:root{
  --gold:#c9a25a;
  --gold-light:#e2c27f;
  --gold-dark:#a9833d;
  --ink:#1c1c1c;
  --dark:#222222;
  --darker:#1a1a1a;
  --text:#3a3a3a;
  --muted:#8a8a8a;
  --paper:#efefef;
  --white:#ffffff;
}
*{box-sizing:border-box;margin:0;padding:0}
html,body{width:1200px;height:2791px;overflow:hidden}
body{position:relative;background:var(--white);font-family:"Barlow",sans-serif;color:var(--text)}
.abs{position:absolute}
h1,h2,h3{font-family:"Poppins",sans-serif}

/* header */
.hero{left:0;top:0;width:1200px;height:599px;background:linear-gradient(100deg,#2b2620 0%,#3d3428 35%,#6d5a3c 65%,#a3864e 85%,#5a4a32 100%)}
.topbar{left:0;top:0;width:1200px;height:75px;background:rgba(20,20,20,.75)}
.brand{left:234px;top:16px;display:flex;align-items:center;gap:12px;font-family:"Barlow",sans-serif;font-weight:700;font-size:22px;color:var(--gold-light);letter-spacing:.5px}
.brand-mark{width:36px;height:36px;background:var(--gold)}
.callout{left:720px;top:18px;display:flex;gap:12px;align-items:center;color:var(--white)}
.callout .icon{width:34px;height:34px;border-radius:50%;background:var(--gold-light);display:flex;align-items:center;justify-content:center}
.callout p{font-size:12px;line-height:17px}
.callout strong{color:var(--gold-light);font-weight:600;font-size:14px}
.nav{left:0;top:75px;width:1200px;height:29px;background:linear-gradient(90deg,var(--gold-light),var(--gold),var(--gold-light))}
.nav ul{list-style:none;display:flex;gap:30px;padding-left:234px;height:29px;align-items:center}
.nav li{font-size:11px;font-weight:600;text-transform:uppercase;color:var(--ink)}
.hero-title{left:234px;top:258px;width:400px;font-size:24px;line-height:31px;font-weight:700;color:var(--white)}
.btn{display:inline-block;background:var(--gold);color:var(--ink);font-size:11px;font-weight:600;text-transform:uppercase;padding:8px 18px;border-radius:2px}
.hero-btn{left:234px;top:407px}
.dots{left:234px;top:572px;display:flex;gap:5px}
.dots span{width:8px;height:8px;border-radius:50%;border:1px solid var(--white)}
.dots span:first-child{background:var(--gold)}

/* who we are */
.dark-band{left:0;top:861px;width:1200px;height:214px;background:var(--darker)}
.who-card{left:225px;top:640px;width:750px;height:245px;background:var(--white)}
.who-photo{left:234px;top:649px;width:356px;height:225px;background:linear-gradient(135deg,#1f1f22,#3a3f48 50%,#15161a)}
.who-text{left:627px;top:645px;width:330px}
.who-text h2{font-size:21px;color:var(--ink);margin-bottom:10px}
.who-text .lead{font-size:13px;line-height:18px;color:var(--ink);font-weight:500;margin-bottom:16px}
.who-text .body{font-size:11px;line-height:17px;color:var(--text);margin-bottom:16px}
.link{font-size:11px;color:var(--gold-dark);border-bottom:1px solid var(--gold);padding-bottom:3px}
.pillar{top:928px;width:232px;display:flex;gap:14px}
.pillar svg{flex:none}
.pillar h3{font-family:"Barlow",sans-serif;font-weight:500;font-size:15px;color:var(--white);margin-bottom:8px}
.pillar p{font-size:11px;line-height:17px;color:#8f8f8f}

/* project */
.project-photo{left:0;top:1075px;width:1200px;height:568px;background:linear-gradient(90deg,#6f7566 0%,#9a8160 30%,#c9a26a 55%,#dcb878 75%,#a98452 100%)}
.project-panel{left:610px;top:1131px;width:356px;height:465px;background:rgba(255,255,255,.95)}
.project-head{left:610px;top:1131px;width:356px;height:65px;background:var(--gold);color:var(--white);font-size:21px;padding:20px 18px}
.project-list{left:610px;top:1206px;width:346px;list-style:none;padding:0 18px}
.project-list li{display:flex;gap:14px;font-size:10.5px;line-height:17px;color:var(--text);padding:12px 0;border-bottom:1px solid #ddd}
.project-list li:last-child{border:0}
.project-list b{color:var(--ink)}
.scroll{left:957px;top:1206px;width:4px;height:130px;background:#333}

/* team */
.team-title{left:0;top:1686px;width:1200px;text-align:center;font-size:21px;color:var(--ink)}
.member{top:1734px;width:152px;height:270px;background:var(--dark)}
.member .photo{width:124px;height:186px;background:linear-gradient(180deg,#d9dde1,#9aa3ac)}
.member .social{position:absolute;left:124px;top:100px;width:28px;height:86px;background:var(--dark);display:flex;flex-direction:column;align-items:center;gap:12px;padding-top:10px}
.member .social span{width:9px;height:9px;background:var(--white)}
.member .info{position:absolute;left:0;top:186px;padding:18px 18px;color:var(--white)}
.member h3{font-family:"Barlow",sans-serif;font-weight:500;font-size:15px}
.member p{font-size:10.5px;color:#bdbdbd;line-height:14px}
.member.active{background:var(--gold)}
.member.active .social{background:var(--gold)}
.member.active p{color:var(--white)}

/* blog + testimonials */
.paper{left:0;top:2056px;width:1200px;height:353px;background:var(--paper)}
.sec-title{font-size:21px;color:var(--ink)}
.post{left:234px;width:360px;display:flex;gap:18px}
.post .thumb{flex:none;width:136px;height:85px}
.post h4{font-size:14px;font-weight:500;color:var(--ink);margin-bottom:4px}
.post .meta{font-size:10px;color:var(--muted);margin-bottom:8px}
.post .meta em{color:var(--gold-dark);font-style:normal}
.post p{font-size:10.5px;line-height:16px;color:var(--text)}
.quote{left:627px;top:2147px;width:339px;height:194px;background:var(--white);padding:18px 18px 18px 48px}
.quote p{font-size:11px;line-height:17px;color:var(--text)}
.quote h5{font-size:13px;font-weight:600;color:var(--ink);margin-top:10px}
.quote small{font-size:10.5px;color:var(--muted)}

/* footer */
.footer{left:0;top:2409px;width:1200px;height:382px;background:linear-gradient(180deg,#2c2c2c,#1e1e1e)}
.skyline{left:0;top:2455px;width:1200px;height:80px;background:linear-gradient(180deg,transparent,#3a3a3a 70%,#2e2e2e)}
.foot-nav{left:0;top:2546px;width:1200px;display:flex;justify-content:center;gap:26px;font-size:11px;color:#cfcfcf}
.foot-col{top:2598px;color:#bdbdbd;font-size:11px;line-height:16px}
.foot-col h4{font-size:13px;font-weight:600;color:var(--white);margin-bottom:6px}
.contact{display:flex;gap:12px;align-items:flex-start}
.contact .icon{flex:none;width:34px;height:34px;border-radius:50%;background:var(--gold-light);display:flex;align-items:center;justify-content:center}
.contact strong{color:var(--white);font-weight:500;font-size:12px}
.field{width:170px;height:30px;background:var(--white);font-size:10px;color:#999;padding:9px 10px;margin:8px 0 6px}
.copyright{left:234px;top:2760px;font-size:10.5px;color:#bdbdbd}
.foot-social{left:850px;top:2754px;display:flex;gap:6px}
.foot-social span{width:22px;height:22px;background:#9a9a9a}
</style>
</head>
<body>

<div class="abs hero" role="img" aria-label="Excavator bucket loading ore beside a haul truck in an open pit mine"></div>
<div class="abs topbar"></div>
<div class="abs brand"><span class="brand-mark"></span>Halverstone Minerals</div>
<div class="abs callout">
  <span class="icon"><svg width="16" height="16" viewBox="0 0 24 24"><path fill="#1c1c1c" d="M6.6 10.8a15 15 0 0 0 6.6 6.6l2.2-2.2c.3-.3.7-.4 1-.2 1.1.4 2.3.6 3.6.6.6 0 1 .4 1 1V20c0 .6-.4 1-1 1A17 17 0 0 1 3 4c0-.6.4-1 1-1h3.5c.6 0 1 .4 1 1 0 1.3.2 2.5.6 3.6.1.3 0 .7-.2 1z"/></svg></span>
  <p>Have a question? call us today<br><strong>+224 600 418 207 &nbsp;|&nbsp; +61 400 772 316</strong></p>
</div>
<nav class="abs nav"><ul><li>Executive Summary</li><li>Team &amp; Experience</li><li>Commercial</li><li>Business Model</li><li>Strategy</li><li>Contact</li></ul></nav>
<h1 class="abs hero-title">A platform for execution of global mining projects with an initial focus on South America, Central America &amp; Africa.</h1>
<span class="abs btn hero-btn">Get Started</span>
<div class="abs dots"><span></span><span></span><span></span><span></span><span></span></div>

<div class="abs dark-band"></div>
<div class="abs who-card"></div>
<div class="abs who-photo" role="img" aria-label="Miners in hard hats inside an underground tunnel"></div>
<div class="abs who-text">
  <h2>Who We Are</h2>
  <p class="lead">Strong industry connections &amp; networks in Africa, South America &amp; Australia.</p>
  <p class="body">Newly formed company to create a platform for execution of global mining projects with an initial focus on South America, Central America &amp; Africa. Strong executive &amp; management team with A to Z in all facets of mining, finance &amp; operations. Properly capitalized to execute its mandate.</p>
  <span class="link">Learn More About Us &nbsp;&rarr;</span>
</div>

<div class="abs pillar" style="left:234px">
  <svg width="34" height="34" viewBox="0 0 34 34" fill="none" stroke="#c9a25a" stroke-width="2"><circle cx="17" cy="17" r="14"/><circle cx="17" cy="17" r="8"/><circle cx="17" cy="17" r="2" fill="#c9a25a"/></svg>
  <div><h3>Our Mission</h3><p>Class aptent taciti sociosqu ad litora torquent per inceptos aeos mauris ut aliquam massa nisl quis neques suspendisse in orci enim.</p></div>
</div>
<div class="abs pillar" style="left:484px">
  <svg width="38" height="34" viewBox="0 0 38 34" fill="none" stroke="#c9a25a" stroke-width="2"><path d="M2 17c5-8 10-11 17-11s12 3 17 11c-5 8-10 11-17 11S7 25 2 17z"/><circle cx="19" cy="17" r="5"/></svg>
  <div><h3>Our Vision</h3><p>Class aptent taciti sociosqu ad litora torquent per inceptos aeos mauris ut aliquam massa nisl quis neques suspendisse in orci enim.</p></div>
</div>
<div class="abs pillar" style="left:733px">
  <svg width="34" height="34" viewBox="0 0 34 34" fill="none" stroke="#c9a25a" stroke-width="2"><path d="M4 30h26M8 30V20M15 30V13M22 30V17M29 30V6"/></svg>
  <div><h3>Our Strategy</h3><p>Class aptent taciti sociosqu ad litora torquent per inceptos aeos mauris ut aliquam massa nisl quis neques suspendisse in orci enim.</p></div>
</div>

<div class="abs project-photo" role="img" aria-label="Worker in a hard hat on red stairway railings overlooking an open pit mine at sunset"></div>
<div class="abs project-panel"></div>
<h2 class="abs project-head">Project Experience</h2>
<ul class="abs project-list">
  <li><svg width="16" height="16" viewBox="0 0 16 16" fill="none" stroke="#c9a25a" stroke-width="1.5"><path d="M2 5c4-3 8-3 12 0M8 3.5 3 14"/></svg><span>Exploration experts in <b>Brazil, Burkina Faso, Cote d'Ivoire, Colombia, Chile, Ghana, Guinea, Gabon, Togo, Mali, Niger, Nigeria, Peru, Saudi Arabia</b> &amp; more recently the copper belt in <b>Zambia.</b></span></li>
  <li><svg width="16" height="16" viewBox="0 0 16 16" fill="none" stroke="#c9a25a" stroke-width="1.5"><path d="M2 5c4-3 8-3 12 0M8 3.5 3 14"/></svg><span><b>Corrow Ridge Mine</b> - an underground polymetallic (Zinc, lead, gold &amp; copper) mine located in the township of Corrow, on Tasmania's west coast, Australia. 2017 production target: over 65,000 tonnes of zinc in zinc concentrate over 18,000 tonnes of lead.</span></li>
  <li><svg width="16" height="16" viewBox="0 0 16 16" fill="none" stroke="#c9a25a" stroke-width="1.5"><path d="M2 5c4-3 8-3 12 0M8 3.5 3 14"/></svg><span><b>Alto Verde mine</b> - a long-life open pit copper mine located in Quispe Valley, Apurimac region of Peru. Target production rate - over 420K tonnes copper per year.</span></li>
  <li><svg width="16" height="16" viewBox="0 0 16 16" fill="none" stroke="#c9a25a" stroke-width="1.5"><path d="M2 5c4-3 8-3 12 0M8 3.5 3 14"/></svg><span>The <b>Serra Clara</b> facility in South East Brazil with an installed capacity to produce approximately 6 million tons of iron ore annually from the Tapera &amp; Jatoba mines &amp; Brejo Mines belonging to Ferrovale Brazil.</span></li>
</ul>
<div class="abs scroll"></div>

<h2 class="abs team-title">Executive Team</h2>
<div class="abs member" style="left:234px"><div class="photo" role="img" aria-label="Portrait of the chairman"></div><div class="social"><span></span><span></span><span></span></div><div class="info"><h3>Owen Hartley</h3><p>Chairman</p></div></div>
<div class="abs member" style="left:422px"><div class="photo" role="img" aria-label="Portrait of the chief executive"></div><div class="social"><span></span><span></span><span></span></div><div class="info"><h3>Marcus Dalby</h3><p>CEO</p></div></div>
<div class="abs member active" style="left:610px"><div class="photo" role="img" aria-label="Portrait of the chief financial officer"></div><div class="social"><span></span><span></span><span></span></div><div class="info"><h3>Graham Pell</h3><p>CFO</p></div></div>
<div class="abs member" style="left:797px;width:178px"><div class="photo" style="width:150px" role="img" aria-label="Portrait of the technical director"></div><div class="social" style="left:150px"><span></span><span></span><span></span></div><div class="info"><h3>Rafael Moura Teixeira</h3><p>Technical Director &amp; Country<br>Manager (Brazil)</p></div></div>

<div class="abs paper"></div>
<h2 class="abs sec-title" style="left:234px;top:2097px">From the Blog</h2>
<div class="abs post" style="top:2147px"><div class="thumb" role="img" aria-label="Miners underground" style="background:linear-gradient(135deg,#22242a,#4a4f58)"></div><div><h4>Lorem Ipsum charsets layouts</h4><p class="meta">By <em>Peter Lund</em> | 03 May 2019</p><p>Class aptent taciti sociosqu ad litora torquent per conubia himenaeos. Mauris in erat justo.</p></div></div>
<div class="abs post" style="top:2260px"><div class="thumb" role="img" aria-label="Haul trucks on a mine road" style="background:linear-gradient(180deg,#c7cdd2,#8d8576 60%,#6d6355)"></div><div><h4>Lorem Ipsum charsets layouts</h4><p class="meta">By <em>Peter Lund</em> | 03 May 2019</p><p>Class aptent taciti sociosqu ad litora torquent per conubia himenaeos. Mauris in erat justo.</p></div></div>
<h2 class="abs sec-title" style="left:627px;top:2097px">Testimonials</h2>
<div class="abs quote">
  <svg class="abs" style="left:16px;top:20px" width="20" height="14" viewBox="0 0 20 14" fill="none" stroke="#8a8a8a" stroke-width="1.5"><path d="M8 2C4 3 2 6 2 9a3 3 0 1 0 3-3M18 2c-4 1-6 4-6 7a3 3 0 1 0 3-3"/></svg>
  <p>Class aptent taciti sociosqu ad litora torquent per conubia nostra, per inceptos himenaeos. Mauris in condimentum sit amet a augue. Sed non neque elit. Sed ut imperdiet nisi. Proin condimentum fermentum nunc. Etiam pharetra, erat sed fermentum feugiat, velit mauris egestas quam, ut aliquam massa nisl quis neque. Suspendisse in orci enim.</p>
  <h5>- Daniel Crowe</h5><small>Lorem ipsum dolor</small>
</div>

<div class="abs footer"></div>
<div class="abs skyline" role="img" aria-label="Silhouettes of mining machinery and workers along the horizon"></div>
<div class="abs foot-nav"><span>Executive Summary</span><span>Team &amp; Experience</span><span>Commercial</span><span>Business Model</span><span>Strategy</span><span>Contact</span></div>
<div class="abs foot-col" style="left:234px;width:140px"><h4>Dubai, UAE</h4>Office 210, Building 3,<br>Marina Court offices,<br>Harbour Walk,<br>Old town Quay,<br>Creekside District,<br>Dubai, UAE.</div>
<div class="abs foot-col" style="left:383px;width:150px"><h4>Guinea, West Africa</h4>Ratoma - Rue du Marché<br>Central<br>Batiment 112,<br>BP: 4417</div>
<div class="abs foot-col" style="left:545px;width:220px">
  <div class="contact"><span class="icon"><svg width="16" height="16" viewBox="0 0 24 24"><path fill="#1c1c1c" d="M6.6 10.8a15 15 0 0 0 6.6 6.6l2.2-2.2c.3-.3.7-.4 1-.2 1.1.4 2.3.6 3.6.6.6 0 1 .4 1 1V20c0 .6-.4 1-1 1A17 17 0 0 1 3 4c0-.6.4-1 1-1h3.5c.6 0 1 .4 1 1 0 1.3.2 2.5.6 3.6.1.3 0 .7-.2 1z"/></svg></span><div>Call Us :<br><strong>+224 600 418 207<br>+61 400 772 316</strong></div></div>
  <div class="contact" style="margin-top:22px"><span class="icon"><svg width="16" height="12" viewBox="0 0 16 12" fill="none" stroke="#1c1c1c" stroke-width="1.6"><rect x="1" y="1" width="14" height="10"/><path d="M1 1l7 6 7-6"/></svg></span><div>Email Us :<br><strong>info@halverstoneminerals.com</strong></div></div>
</div>
<div class="abs foot-col" style="left:796px;width:180px"><h4>Subscribe Newsletter</h4><div class="field">Email Address</div><span class="btn" style="padding:7px 14px;font-size:10px">Subscribe</span></div>
<div class="abs copyright">&copy; 2018 Halverstone Minerals. All Rights Reserved</div>
<div class="abs foot-social"><span></span><span></span><span></span><span></span></div>

</body>
</html>
```